Website redesign for AI startup

Overview
We are looking to have our website https://www.hellomarlo.ai/ redesigned to look much more sophisticated and modern. We would like the brand colors to be different and less or no use of the Marlo bird character. We have included some example sites below for designs that we like. Please do not to use the same purple or purple at all on the site as we would like different brand colors and 'too much purple' has been the main comment.

Example sites that we like:
https://www.quorvant.com/
https://pagemorrow.com/
https://www.steadycloudly.com/

Requirements
Redesign the following pages from our website, modeling an example site that we like:
-Home page: https://hellomarlo.ai
-See an example: https://www.hellomarlo.ai/example-page
-Pricing: https://www.hellomarlo.ai/pricing
-Product: https://www.hellomarlo.ai/how-it-works
-Portal home: https://www.hellomarlo.ai/overview (you will need to create an account to view this; the account is free)
New design should be sleek, professional, and modern
The pages should contain the same content that it currently does.
Images on the pages should change to match the new designs and style.
Use different brand colors, these should look professional
The Marlo bird character can be used, but it’s not required. If the bird is used, it should be rarely used and not front-and-center.
Provide both desktop and mobile designs

Target Market(s)

Small business owners

Industry/Entity Type

SaaS tool

Number of Pages Required

5+ page

Requirements
Must have
• modern and sleek design, different brand colors, mobile and web designs

```html
<!DOCTYPE html>
<html lang="en">
<head>
<meta charset="utf-8">
<title>helloMarlo – Your 24/7 AI Sales Assistant</title>
<link rel="stylesheet" href="https://fonts.googleapis.com/css2?family=Outfit:wght@300;400;500;600;700;800&display=swap">
<style>
:root{
  --navy:#0c1a2b;
  --ink:#132233;
  --muted:#5f6b78;
  --mist:#e7f1ef;
  --mist-2:#d3e6e2;
  --teal:#2f8f86;
  --teal-deep:#1f6f68;
  --sand:#f4e3ad;
  --white:#ffffff;
  --line:#d5dde0;
}
*{box-sizing:border-box;margin:0;padding:0}
html,body{width:1200px;height:3416px;overflow:hidden;background:var(--white)}
body{font-family:"Outfit",sans-serif;color:var(--ink);position:relative}
.abs{position:absolute}
.center{left:0;width:1200px;text-align:center}
a{color:inherit;text-decoration:none}

.hero-bg{left:0;top:0;width:1200px;height:755px;
  background:radial-gradient(circle at 1180px 420px,#8cc7bf 0,rgba(140,199,191,0) 320px),
             linear-gradient(180deg,#cfe5e1 0,#e7f1ef 60%,#edf5f3 100%)}
.logo{left:110px;top:34px;font-size:36px;font-weight:800;letter-spacing:-.5px;color:var(--ink)}
.nav{left:412px;top:46px;display:flex;font-size:17px;color:#34465a}
.nav a{margin-right:24px}
.nav a.active{font-weight:600;color:var(--ink)}
.btn{display:flex;align-items:center;justify-content:center;border-radius:8px;font-weight:600;font-size:18px}
.btn-dark{background:var(--navy);color:var(--white)}
.btn-grad{background:linear-gradient(90deg,#7fbcb4 0,var(--sand) 100%);color:var(--navy);border:1.5px solid var(--navy)}
.login{left:990px;top:37px;width:98px;height:43px}

.welcome{top:150px;font-size:31px;font-weight:600}
.hero-title{top:196px;font-size:43px;font-weight:700;line-height:46px}
.hero-sub{top:304px;font-size:34px;font-weight:300}
.cta1{left:384px;top:374px;width:201px;height:44px}
.cta2{left:598px;top:374px;width:218px;height:44px}

.preview{left:173px;top:505px;width:854px;height:453px;border-radius:10px;
  background:linear-gradient(160deg,#1c3145 0,#2d5661 55%,#4f8f88 100%)}
.play{left:555px;top:686px;width:90px;height:90px;border-radius:50%;background:rgba(231,241,239,.85)}

.section-title{font-size:43px;font-weight:700;line-height:45px}
.section-sub{font-size:34px;font-weight:300;line-height:45px}
.start-title{top:1063px}
.start-sub{top:1165px}
.trial{left:491px;top:1282px;width:218px;height:42px}

.feature-card{left:112px;top:1417px;width:456px;height:205px;background:var(--mist);border-bottom:4px solid var(--teal-deep);border-radius:4px}
.feature-card h3{position:absolute;left:90px;top:43px;font-size:20px;font-weight:600}
.feature-card p{position:absolute;left:39px;top:86px;width:372px;font-size:18px;line-height:28px;color:#253545}
.feature-card p u{text-decoration:underline}
.feat-item{left:146px;display:flex;align-items:center;font-size:20px;font-weight:500;line-height:26px}
.feat-item svg{margin-right:22px;flex:none}

.visual{left:600px;top:1417px;width:600px;height:635px;
  background:radial-gradient(circle at 600px 635px,#84c1b9 0,rgba(132,193,185,0) 380px),linear-gradient(180deg,#e3efed,#d3e6e2)}

.test-title{top:2178px}
.stars{top:2330px;font-size:14px;color:#e0a800;letter-spacing:3px}
.quote{left:270px;top:2370px;width:660px;text-align:center;font-size:23.5px;line-height:34.5px;color:#253545}
.author{top:2530px;font-size:21px;font-weight:500}
.faded{font-size:15px;line-height:25px;color:#aab3bb}
.arrow{width:40px;height:40px;border-radius:50%;background:var(--sand);border:1.5px solid var(--navy);display:flex;align-items:center;justify-content:center}

.cta-band{left:0;top:2736px;width:1200px;height:377px;
  background:radial-gradient(circle at 1200px 377px,#82bfb7 0,rgba(130,191,183,0) 340px),linear-gradient(180deg,#d3e6e2,#e7f1ef)}
.cta-title{top:2788px}
.cta-sub{top:2890px}
.cta-btn{left:487px;top:3007px;width:227px;height:43px}

footer{position:absolute;left:0;top:3113px;width:1200px;height:303px;background:var(--navy);color:#fff}
.f-logo{left:115px;top:56px;font-size:52px;font-weight:800;letter-spacing:-.5px}
.f-col h4{font-size:16px;font-weight:700;letter-spacing:.3px;margin-bottom:14px}
.f-col a{display:block;font-size:16px;line-height:27px}
.social{width:36px;height:36px;border:1.5px solid #fff;border-radius:50%}
.copy{top:222px;font-size:16px}
</style>
</head>
<body>

<div class="abs hero-bg"></div>
<div class="abs logo">helloMarlo</div>
<nav class="abs nav">
  <a class="active" href="#">Home</a><a href="#">Product</a><a href="#">Support</a><a href="#">Pricing</a><a href="#">FAQ</a><a href="#">Referral</a><a href="#">Program</a>
</nav>
<a class="abs btn btn-dark login" href="#">Log in</a>

<div class="abs center welcome">Welcome!</div>
<h1 class="abs center hero-title">Save time and get more customers<br>with helloMarlo</h1>
<div class="abs center hero-sub">Your 24/7 AI Sales Assistant</div>
<a class="abs btn btn-dark cta1" href="#">See an Example!</a>
<a class="abs btn btn-grad cta2" href="#">Create your Marlo</a>

<div class="abs preview" role="img" aria-label="Product video preview of the assistant settings dashboard"></div>
<div class="abs play"></div>
<svg class="abs" style="left:570px;top:701px" width="60" height="60" viewBox="0 0 60 60"><circle cx="30" cy="30" r="30" fill="#0c1a2b"/><circle cx="30" cy="30" r="19" fill="none" stroke="#fff" stroke-width="3"/><path d="M25 21 L39 30 L25 39Z" fill="#fff"/></svg>

<h2 class="abs center section-title start-title">We’ll help you<br>get started</h2>
<p class="abs center section-sub start-sub">helloMarlo benefits both you and<br>your customers equally.</p>
<a class="abs btn btn-grad trial" href="#">14-Day Free Trial</a>

<div class="abs feature-card">
  <svg style="position:absolute;left:38px;top:36px" width="40" height="36" viewBox="0 0 40 36" fill="none" stroke="#132233" stroke-width="1.6"><path d="M32 14 A15 15 0 1 0 18 33"/><path d="M17 9 V18 H24"/><text x="22" y="34" font-size="13" fill="#132233" stroke="none" font-family="Outfit,sans-serif">24</text></svg>
  <h3>24/7 Customer Engagement</h3>
  <p>Marlo interacts with your leads across email, chatbot, phone, and text around the clock. <u>See an example here.</u></p>
</div>

<div class="abs feat-item" style="top:1668px">
  <svg width="46" height="40" viewBox="0 0 46 40" fill="none" stroke="#132233" stroke-width="1.6"><rect x="6" y="4" width="36" height="8"/><rect x="2" y="16" width="42" height="8"/><rect x="10" y="28" width="26" height="8"/></svg>
  <span>Lead Qualification &amp;<br>Prioritization</span></div>
<div class="abs feat-item" style="top:1761px">
  <svg width="46" height="40" viewBox="0 0 46 40" fill="none" stroke="#132233" stroke-width="1.6"><rect x="4" y="6" width="30" height="28" rx="2"/><path d="M4 14 H34 M11 2 V9 M27 2 V9"/><circle cx="32" cy="28" r="9" fill="#fff"/><path d="M32 23 V28 H36"/></svg>
  <span>Automated Scheduling</span></div>
<div class="abs feat-item" style="top:1850px">
  <svg width="46" height="40" viewBox="0 0 46 40" fill="none" stroke="#132233" stroke-width="1.6"><path d="M8 22 C2 18 6 8 14 9 C16 3 26 3 28 8 C36 6 42 14 38 20 C42 26 36 34 30 31 C26 37 16 36 14 31 C6 33 2 26 8 22Z"/><path d="M14 17 L22 20 L30 14 M22 20 L24 29"/></svg>
  <span>Rapid and Effective AI<br>Training</span></div>
<div class="abs feat-item" style="top:1940px">
  <svg width="46" height="40" viewBox="0 0 46 40" fill="none" stroke="#132233" stroke-width="1.6"><path d="M4 8 H42 M4 20 H42 M4 32 H42"/><path d="M30 3 V13 M14 15 V25 M24 27 V37"/></svg>
  <span>Customize Your Assistant</span></div>
<div class="abs feat-item" style="top:2018px">
  <svg width="46" height="40" viewBox="0 0 46 40" fill="none" stroke="#132233" stroke-width="1.6"><path d="M4 10 H16 V6 H22 V10 H30 V6 H36 V10 H42 V32 H30 V28 H24 V32 H14 V28 H8 V32 H4Z"/><path d="M14 18 L20 24 L30 16"/></svg>
  <span>Seamless Tool Integration</span></div>

<div class="abs visual" role="img" aria-label="Business owner on a laptop chatting with the assistant, with call and message cards"></div>

<h2 class="abs center section-title test-title">What People are Saying<br>About Us</h2>
<div class="abs center stars">★★★★★</div>
<p class="abs quote">helloMarlo is a gamechanger for small businesses looking to streamline their sales pipeline and handle customer conversations. The future is AI and helloMarlo is leading the change in this space</p>
<div class="abs center author">Reid Calloway, Founder</div>

<div class="abs faded" style="left:0;top:2356px;font-size:11px;color:#e8c55a;letter-spacing:2px">★ ★ ★</div>
<div class="abs faded" style="left:-6px;top:2389px;width:230px">ring, lead qualification, and<br>olve the broken sales and<br>r small businesses. This is a<br>ne and my clients.</div>
<div class="abs faded" style="left:0;top:2506px;font-size:16px;color:#97a1aa">Marketing Strategist</div>
<div class="abs faded" style="left:1164px;top:2356px;font-size:11px;color:#e8c55a;letter-spacing:2px">★ ★ ★</div>
<div class="abs faded" style="left:974px;top:2389px;width:240px;text-align:right;white-space:nowrap">There’s no other AI assistant<br>Best kept sec</div>
<div class="abs faded" style="left:1092px;top:2506px;font-size:16px;color:#97a1aa;white-space:nowrap">Owen Marsh,</div>

<div class="abs arrow" style="left:550px;top:2630px"><svg width="12" height="14" viewBox="0 0 12 14"><path d="M8 2 L3 7 L8 12" stroke="#0c1a2b" stroke-width="1.6" fill="none"/></svg></div>
<div class="abs arrow" style="left:610px;top:2630px"><svg width="12" height="14" viewBox="0 0 12 14"><path d="M4 2 L9 7 L4 12" stroke="#0c1a2b" stroke-width="1.6" fill="none"/></svg></div>

<div class="abs cta-band"></div>
<h2 class="abs center section-title cta-title">SET UP<br>your own Marlo</h2>
<p class="abs center section-sub cta-sub">Create your own Marlo in just seconds here and<br>share it on your social media, website, and more!</p>
<a class="abs btn btn-dark cta-btn" href="#">Create your Marlo</a>

<footer>
  <div class="abs f-logo">helloMarlo</div>
  <div class="abs social" style="left:113px;top:170px" aria-label="Social profile 1"></div>
  <div class="abs social" style="left:168px;top:170px" aria-label="Social profile 2"></div>
  <div class="abs social" style="left:222px;top:170px" aria-label="Social profile 3"></div>
  <div class="abs social" style="left:277px;top:170px" aria-label="Social profile 4"></div>
  <div class="abs f-col" style="left:465px;top:62px"><h4>QUICK LINKS</h4><a href="#">Home</a><a href="#">Product</a><a href="#">Support</a></div>
  <div class="abs f-col" style="left:688px;top:62px"><h4>OTHER LINKS</h4><a href="#">Pricing</a><a href="#">FAQ</a><a href="#">Referral Program</a></div>
  <div class="abs f-col" style="left:951px;top:62px"><h4>LEGALR LINKS</h4><a href="#">Give feedback</a><a href="#">Privacy Policy</a><a href="#">Terms of Use</a></div>
  <div class="abs center copy">© 2024 HelloMarlo.ai. All rights reserved.</div>
</footer>

</body>
</html>
```